KORV PTY LTD - Business Cards

Design a modern business card - using the attached Designs.
Same design as on the front, apart from the names/numbers/emails to be different.
We want the cards to be very glossy to stand out, do I think the simple black/white/metallic will be effective.
Both lots of details below:

Tom Wrenshaw
Director
tom_korv@nulvane.com
0438 274 093

Lewis Corbyn
Director
lewis_korv@nulvane.com
0419 385 642

Industry/Entity Type

Business

```html
<!DOCTYPE html>
<html lang="en">
<head>
<meta charset="utf-8">
<title>KORV PTY LTD – Business Cards</title>
<link href="https://fonts.googleapis.com/css2?family=Bitter:wght@400;700&family=Open+Sans:wght@400&display=swap" rel="stylesheet">
<style>
  :root {
    --stage: #e9e7e4;
    --card-white: #ffffff;
    --charcoal: #2b3035;
    --stripe-grey: #b9bcbc;
    --rule-grey: #c9c9c9;
    --ink: #2e3236;
    --metal-dark: #9c9a9f;
    --metal-mid: #c8c6cb;
    --metal-light: #f2f2f4;
  }
  * { box-sizing: border-box; margin: 0; padding: 0; }
  html, body { width: 1200px; height: 475px; overflow: hidden; }
  body {
    background: var(--stage);
    position: relative;
    font-family: "Bitter", Georgia, serif;
  }
  .card {
    position: absolute;
    top: 82px;
    width: 520px;
    height: 310px;
    overflow: hidden;
    box-shadow: 0 6px 18px rgba(0,0,0,0.18);
  }
  .card--front { left: 50px; background: var(--card-white); }
  .card--back {
    left: 630px;
    background: linear-gradient(90deg,
      var(--metal-dark) 0%, var(--metal-mid) 22%, var(--metal-light) 45%,
      var(--metal-mid) 62%, var(--metal-dark) 80%, var(--metal-mid) 100%);
  }
  .header-band { position: absolute; left: 0; top: 0; width: 520px; height: 110px; }
  .brand {
    position: absolute;
    left: 50%;
    transform: translateX(-50%);
    display: flex;
    align-items: center;
    gap: 12px;
  }
  .card--front .brand { top: 40px; }
  .card--back .brand { top: 50%; transform: translate(-50%, -50%); }
  .brand__dot {
    border-radius: 50%;
    background: var(--charcoal);
  }
  .card--front .brand__dot { width: 26px; height: 26px; }
  .card--back .brand__dot { width: 38px; height: 38px; }
  .brand__name {
    font-family: "Bitter", Georgia, serif;
    font-weight: 700;
    color: var(--charcoal);
    letter-spacing: 2px;
  }
  .card--front .brand__name { font-size: 44px; }
  .card--back .brand__name { font-size: 64px; }
  .card--front .brand__wrap {
    background: var(--card-white);
    padding: 6px 20px;
    border-radius: 40px;
    display: flex; align-items: center; gap: 12px;
  }
  .details {
    position: absolute;
    left: 0; right: 0;
    top: 188px;
    text-align: center;
    color: var(--ink);
  }
  .details__name { font-size: 19px; font-weight: 700; }
  .details__role { font-size: 15px; font-weight: 400; }
  .details__rule {
    width: 190px; height: 1px; margin: 9px auto 10px;
    background: var(--rule-grey);
  }
  .details__line {
    font-family: "Open Sans", Arial, sans-serif;
    font-size: 15px;
    line-height: 22px;
    display: flex; justify-content: center; align-items: center; gap: 6px;
  }
  .details__icon { width: 13px; height: 13px; fill: var(--ink); }
</style>
</head>
<body>
  <section class="card card--front" aria-label="Business card front">
    <svg class="header-band" viewBox="0 0 520 110" aria-hidden="true">
      <polygon points="0,0 520,0 520,46 0,96" fill="var(--charcoal)"/>
      <polygon points="0,96 520,46 520,54 0,104" fill="var(--stripe-grey)"/>
    </svg>
    <div class="brand">
      <div class="brand__wrap">
        <span class="brand__dot"></span>
        <span class="brand__name">KORV</span>
      </div>
    </div>
    <div class="details">
      <p><span class="details__name">Lewis Corbyn,</span> <span class="details__role">Director</span></p>
      <div class="details__rule"></div>
      <p class="details__line">
        <svg class="details__icon" viewBox="0 0 16 16" aria-hidden="true"><path d="M3.5 1h3l1.2 3.5-1.8 1.3a9 9 0 0 0 4.3 4.3l1.3-1.8L15 9.5v3a2 2 0 0 1-2 2C6.9 14.5 1.5 9.1 1.5 3a2 2 0 0 1 2-2z"/></svg>
        0419 385 642
      </p>
      <p class="details__line">
        <svg class="details__icon" viewBox="0 0 16 16" aria-hidden="true"><path d="M1 5l7-4 7 4v9H1z M2.5 6l5.5 4 5.5-4" stroke="#fff" stroke-width="1"/></svg>
        lewis_korv@nulvane.com
      </p>
    </div>
  </section>

  <section class="card card--back" aria-label="Business card back">
    <div class="brand">
      <span class="brand__dot"></span>
      <span class="brand__name">KORV</span>
    </div>
  </section>
</body>
</html>
```